Business card design for my company.
I would like the card's background colour to be black. You can also see our web site to get an idea of our brand. https://www.tmwhomecrafting.com.au/
- Name
- Email

```html
<!DOCTYPE html>
<html lang="en">
<head>
<meta charset="UTF-8">
<title>TMW Home Crafting – Business Card</title>
<link href="https://fonts.googleapis.com/css2?family=Montserrat:wght@400;600;700&display=swap" rel="stylesheet">
<style>
  :root {
    --card-black: #222222;
    --page-bg: #e9e9e9;
    --brand-green: #1a9a48;
    --text-white: #f4f4f4;
    --band-white: #f7f7f7;
  }
  * { box-sizing: border-box; margin: 0; padding: 0; }
  html, body {
    width: 1200px; height: 912px; overflow: hidden;
    background: var(--page-bg);
    font-family: "Montserrat", sans-serif;
  }
  .sheet {
    position: relative; width: 1200px; height: 912px;
  }
  .card {
    position: absolute; width: 600px; height: 343px;
    background: var(--card-black);
    border-radius: 14px; overflow: hidden;
    box-shadow: 0 10px 24px rgba(0,0,0,0.25);
  }
  .card--front { left: 120px; top: 90px; }
  .card--back { left: 480px; top: 479px; }

  .brand {
    display: flex; align-items: center; gap: 12px;
    color: var(--text-white); font-weight: 700;
    letter-spacing: 0.06em; text-transform: uppercase;
  }
  .brand__mark {
    width: 18px; height: 18px; background: var(--brand-green);
  }
  .card--front .brand {
    position: absolute; left: 0; right: 0; top: 0; bottom: 0;
    justify-content: center; font-size: 30px;
  }
  .card--back .brand {
    position: absolute; left: 44px; top: 72px; font-size: 20px;
  }
  .card--back .brand__mark { width: 14px; height: 14px; }

  .back-art { position: absolute; inset: 0; }

  .person {
    position: absolute; right: 48px; top: 92px; text-align: right;
  }
  .person__name {
    color: var(--brand-green); font-weight: 700; font-size: 24px;
    letter-spacing: 0.02em; text-transform: uppercase;
  }
  .person__role {
    color: var(--text-white); font-weight: 400; font-size: 14px; margin-top: 2px;
  }

  .contacts {
    position: absolute; left: 48px; top: 212px;
    list-style: none; color: var(--text-white);
    font-size: 15px; font-weight: 400;
  }
  .contacts__item {
    display: flex; align-items: center; gap: 10px; height: 24px;
  }
  .contacts__icon { width: 14px; height: 14px; flex: none; }
  .contacts__accent { color: var(--brand-green); }
</style>
</head>
<body>
<main class="sheet">

  <section class="card card--front" aria-label="Card front">
    <div class="brand"><span class="brand__mark"></span>TMW Home Crafting</div>
  </section>

  <section class="card card--back" aria-label="Card back">
    <svg class="back-art" width="600" height="343" viewBox="0 0 600 343" aria-hidden="true">
      <line x1="48" y1="202" x2="400" y2="150" stroke="var(--brand-green)" stroke-width="1.5"/>
      <rect x="566" y="90" width="34" height="44" fill="var(--brand-green)"/>
      <polygon points="0,318 420,318 410,343 0,343" fill="var(--brand-green)"/>
      <polygon points="430,318 600,318 600,343 420,343" fill="var(--band-white)"/>
    </svg>

    <div class="brand"><span class="brand__mark"></span>TMW Home Crafting</div>

    <div class="person">
      <p class="person__name">Daniel Reyes</p>
      <p class="person__role">CEO/Founder</p>
    </div>

    <ul class="contacts">
      <li class="contacts__item">
        <svg class="contacts__icon" viewBox="0 0 24 24" aria-hidden="true"><path fill="var(--brand-green)" d="M6.6 10.8a15 15 0 0 0 6.6 6.6l2.2-2.2a1 1 0 0 1 1-.25 11.4 11.4 0 0 0 3.6.57 1 1 0 0 1 1 1V20a1 1 0 0 1-1 1A17 17 0 0 1 3 4a1 1 0 0 1 1-1h3.5a1 1 0 0 1 1 1c0 1.25.2 2.45.57 3.57a1 1 0 0 1-.25 1z"/></svg>
        897-555-0142
      </li>
      <li class="contacts__item">
        <svg class="contacts__icon" viewBox="0 0 24 24" aria-hidden="true"><rect x="2" y="5" width="20" height="14" fill="var(--brand-green)"/><path d="M2 5l10 8 10-8" fill="none" stroke="var(--card-black)" stroke-width="1.5"/></svg>
        info@tmwhomecrafting.com.au
      </li>
      <li class="contacts__item">
        <svg class="contacts__icon" viewBox="0 0 24 24" aria-hidden="true"><g fill="none" stroke="var(--brand-green)" stroke-width="2"><circle cx="12" cy="12" r="9"/><ellipse cx="12" cy="12" rx="4" ry="9"/><line x1="3" y1="12" x2="21" y2="12"/></g></svg>
        <span>www.<span class="contacts__accent">tmwhomecrafting</span>.com.au</span>
      </li>
    </ul>
  </section>

</main>
</body>
</html>
```